Oil and Gas Exploration and Production company needs a business card design

We need a business card design using our logo and colors in the logo. We want a mainstream design.

```html
<!DOCTYPE html>
<html lang="en">
<head>
<meta charset="utf-8">
<title>Zenta Oil &amp; Gas — Business Card</title>
<link rel="stylesheet" href="https://fonts.googleapis.com/css2?family=Open+Sans:wght@400;600;700;800&display=swap">
<style>
  :root {
    --bg: #d9d9d9;
    --card: #ffffff;
    --ink: #141414;
    --band: #2b2b2b;
    --gold: #e0a021;
    --divider: #8a8a8a;
    --shadow: rgba(0,0,0,0.18);
  }
  * { box-sizing: border-box; margin: 0; padding: 0; }
  html, body { width: 1200px; height: 864px; overflow: hidden; }
  body {
    background: var(--bg);
    font-family: "Open Sans", Arial, sans-serif;
    color: var(--ink);
    position: relative;
  }
  .card {
    position: absolute;
    width: 630px;
    height: 360px;
    background: var(--card);
    box-shadow: 0 6px 18px var(--shadow);
    overflow: hidden;
  }
  .card--back { left: 520px; top: 50px; }
  .card--front { left: 50px; top: 454px; }

  .brand {
    position: absolute;
    display: flex;
    align-items: center;
    gap: 14px;
    white-space: nowrap;
  }
  .brand__dot {
    border-radius: 50%;
    background: var(--gold);
    flex: none;
  }
  .brand__name {
    font-weight: 800;
    color: var(--ink);
    letter-spacing: -0.5px;
  }
  .card--back .brand { left: 0; right: 0; top: 140px; justify-content: center; }
  .card--back .brand__dot { width: 44px; height: 44px; }
  .card--back .brand__name { font-size: 56px; }
  .back__glow {
    position: absolute;
    width: 300px; height: 300px;
    left: 270px; top: 40px;
    border-radius: 50%;
    background: #f4f2ee;
  }

  .card--front .brand { left: 0; right: 0; top: 34px; justify-content: center; }
  .card--front .brand__dot { width: 32px; height: 32px; }
  .card--front .brand__name { font-size: 42px; }

  .rule { position: absolute; left: 0; right: 0; height: 3px; background: var(--gold); }
  .rule--top { top: 130px; }
  .rule--bottom { top: 206px; }
  .band {
    position: absolute;
    left: 0; right: 0; top: 140px; height: 58px;
    background: var(--band);
    display: flex; align-items: center; justify-content: center;
    gap: 22px;
    color: var(--gold);
  }
  .band__name { font-size: 24px; font-weight: 600; }
  .band__sep { width: 2px; height: 30px; background: #f0f0f0; transform: skewX(-15deg); }
  .band__role { font-size: 17px; }

  .contacts {
    position: absolute;
    left: 40px; top: 240px; width: 250px;
    list-style: none;
    text-align: right;
    font-size: 16px;
    line-height: 27px;
  }
  .contacts li { display: flex; justify-content: flex-end; align-items: center; gap: 10px; }
  .icon { width: 16px; height: 16px; flex: none; }
  .divider {
    position: absolute;
    left: 315px; top: 236px;
    width: 2px; height: 92px;
    background: var(--divider);
  }
  .address {
    position: absolute;
    left: 340px; top: 240px;
    display: flex; gap: 10px;
    font-size: 16px; line-height: 22px;
    font-style: normal;
  }
  .address .icon { margin-top: 3px; }
</style>
</head>
<body>

  <section class="card card--back" aria-label="Card back">
    <div class="back__glow" aria-hidden="true"></div>
    <div class="brand">
      <span class="brand__dot"></span>
      <span class="brand__name">Zenta Oil &amp; Gas</span>
    </div>
  </section>

  <section class="card card--front" aria-label="Card front">
    <div class="brand">
      <span class="brand__dot"></span>
      <span class="brand__name">Zenta Oil &amp; Gas</span>
    </div>

    <div class="rule rule--top"></div>
    <div class="band">
      <span class="band__name">Dale Harmon</span>
      <span class="band__sep"></span>
      <span class="band__role">CEO</span>
    </div>
    <div class="rule rule--bottom"></div>

    <ul class="contacts">
      <li>1 555-210-4837
        <svg class="icon" viewBox="0 0 16 16"><circle cx="8" cy="8" r="8" fill="var(--gold)"/><rect x="4" y="6" width="8" height="5" rx="1" fill="#fff"/><rect x="5.5" y="4.5" width="5" height="2" rx="1" fill="#fff"/></svg>
      </li>
      <li>+1 555-210-0192
        <svg class="icon" viewBox="0 0 16 16"><circle cx="8" cy="8" r="8" fill="var(--gold)"/><path d="M6 4.5c-1 .5-1.5 1.5-1 3 .6 2 2 3.5 4 4 1 .3 2-.2 2.5-1l-1.5-1.2-1 .6c-1-.4-1.8-1.3-2.1-2.3l.7-.9z" fill="#fff"/></svg>
      </li>
      <li>info@zentaoil.com
        <svg class="icon" viewBox="0 0 16 16"><circle cx="8" cy="8" r="8" fill="var(--gold)"/><rect x="4" y="5" width="8" height="6" rx="1" fill="#fff"/><path d="M4.3 5.4 8 8.3l3.7-2.9" fill="none" stroke="var(--gold)" stroke-width="1"/></svg>
      </li>
    </ul>

    <div class="divider"></div>

    <address class="address">
      <svg class="icon" viewBox="0 0 16 16"><circle cx="8" cy="8" r="8" fill="var(--gold)"/><path d="M8 3.5a3 3 0 0 0-3 3c0 2.2 3 5.5 3 5.5s3-3.3 3-5.5a3 3 0 0 0-3-3z" fill="#fff"/><circle cx="8" cy="6.5" r="1.1" fill="var(--gold)"/></svg>
      <span>PO Box 4821, Midland, TX,<br>USA, Odessa, TX 79760-4821<br>Box : 4821</span>
    </address>
  </section>

</body>
</html>
```